Forex website redesign

We need an attractive good looking website design that increase the apatite of our visitors to subscribe to our advisory service, beside the fact that we do offer very high quality service.

Our service is where we connect to investor accounts who are subscribed, to automatically deliver and execute our advise to buy or sell straight onto their account using high tech software.

The final design should communicate financial safty and growth.
Updates

Here is something to keep in mind about our business model that may help you in your design, we SHOW people the right way to invest, so they can make money instead of going somewere else and lose it. Beside that point, most websites in forex that includes pictures of happy and excited people who make money ALWAY turn out to be scam. So please try not to position our business that way in visitor first impression once he/she visit our site.

Thank you for your help :)

Target Market(s)

Financial Market, 20-70 years old

Industry/Entity Type

Financial

Requirements
Must have
• Call to action feature + Logo redesign. Please visit www.veldoramarkets.com to get an idea of how we want it. Also include the personal photos of our advisors in your deign.

```html
<!DOCTYPE html>
<html lang="en">
<head>
<meta charset="utf-8">
<title>Veldora FX Ltd. – Home</title>
<link rel="stylesheet" href="https://fonts.googleapis.com/css2?family=Open+Sans:ital,wght@0,400;0,600;0,700;1,700&family=Oswald:wght@500&family=Ubuntu:ital,wght@0,400;0,500;1,400&display=swap">
<style>
:root{
  --orange:#f7931e;
  --orange-deep:#ef6c0a;
  --ink:#222;
  --text:#555;
  --muted:#9a9a9a;
  --header-bg:#e4e4e4;
  --page-bg:#ececec;
  --panel:#ffffff;
  --footer:#3a3a3a;
  --blue:#1e8fd6;
  --yellow:#f8c21a;
}
*{box-sizing:border-box;margin:0;padding:0}
html,body{width:985px;height:1200px;overflow:hidden}
body{position:relative;background:var(--page-bg);font-family:'Open Sans',sans-serif;color:var(--text)}
.abs{position:absolute}

.topline{left:0;top:0;width:985px;height:3px;background:#3b3b3b}
.header{left:0;top:3px;width:985px;height:96px;background:var(--header-bg)}
.brand{left:198px;top:15px;display:flex;align-items:center;gap:8px}
.brand-mark{width:36px;height:36px;background:var(--orange)}
.brand-name{font-family:'Ubuntu',sans-serif;font-weight:500;font-size:24px;color:#3a3a3a;line-height:1}
.brand-tag{left:245px;top:42px;font-size:9px;color:#555;font-family:'Ubuntu',sans-serif}
.btn-sm{top:26px;height:16px;border-radius:3px;font-size:8px;display:flex;align-items:center;justify-content:center;color:#fff}
.btn-login{left:620px;width:43px;background:var(--blue)}
.btn-register{left:670px;width:43px;background:var(--yellow);color:#7a5200}
.btn-lang{left:720px;width:68px;background:#222;justify-content:flex-start;padding-left:6px}
.btn-lang svg{position:absolute;right:5px;top:6px}
.nav{left:198px;top:64px;width:590px;height:25px;background:#f1f1f1;border:1px solid #d4d4d4;display:flex;align-items:center;justify-content:space-around;font-family:'Ubuntu',sans-serif;font-size:10.5px;color:#333}
.nav .active{border-bottom:2px solid var(--orange);padding-bottom:3px;margin-top:5px}

.hero{left:0;top:99px;width:985px;height:300px;background:linear-gradient(90deg,#6a6258 0%,#8d8173 30%,#55514d 60%,#2f3236 100%)}
.hero-photo{left:175px;top:8px;width:390px;height:270px;background:linear-gradient(180deg,#7b746d,#4a4744);border-radius:4px}
.hero-copy{left:566px;top:192px;font-family:'Oswald',sans-serif;color:#fff}
.hero-l1{font-size:23px;line-height:26px;letter-spacing:-.2px}
.hero-l2{font-size:40px;line-height:44px;color:var(--orange)}
.hero-l3{font-family:'Ubuntu',sans-serif;font-style:italic;font-size:21px;line-height:26px}
.arrow{top:219px}
.arrow-left{left:133px}
.arrow-right{left:818px}
.hero-curve{left:0;top:360px}

.page-pattern{left:0;top:372px;width:985px;height:498px;background:#f2f2f2}
.panel{left:191px;top:372px;width:603px;height:498px;background:var(--panel)}
.intro{left:200px;top:416px;width:585px;text-align:center;font-family:'Ubuntu',sans-serif;font-size:14.3px;line-height:19px;color:var(--ink)}

.signals{left:200px;top:500px;width:586px;height:166px;background:repeating-linear-gradient(45deg,#ececec 0 2px,#e3e3e3 2px 4px);border:1px solid #ddd}
.signals h2{position:absolute;left:14px;top:13px;font-family:'Ubuntu',sans-serif;font-weight:400;font-size:12px;color:#555}
.signals-body{position:absolute;left:14px;top:35px;width:428px;font-size:7.6px;line-height:12.2px;color:#666}
.signals-img{float:left;width:111px;height:56px;margin:0 9px 2px 0;background:linear-gradient(135deg,#2b3a55,#ef7c2a 60%,#3c7fd0)}
.brokers{left:648px;top:510px;width:126px;height:145px;background:#fff;border:1px solid #ddd;border-radius:3px;padding:12px 10px}
.brokers h3{font-family:'Ubuntu',sans-serif;font-weight:400;font-size:11.5px;color:#444;margin-bottom:6px}
.brokers p{font-size:7.6px;line-height:14px;color:#777}

.divider{left:198px;top:698px;width:588px;height:1px;background:#e2e2e2}
.feature{width:180px}
.feature .icon{position:absolute;left:0;top:0;width:40px;height:40px;border:1px solid #ddd;border-radius:3px;background:#fafafa;display:flex;align-items:center;justify-content:center}
.feature h4{position:absolute;left:49px;top:0;font-family:'Ubuntu',sans-serif;font-weight:400;font-size:12.5px;color:#333;white-space:nowrap}
.feature p{position:absolute;left:49px;top:18px;width:130px;font-size:7px;line-height:10px;color:#777}
.f1{left:204px;top:733px}.f2{left:392px;top:733px}.f3{left:204px;top:788px}.f4{left:392px;top:788px}

.register{left:598px;top:728px;width:178px;height:108px;background:#f6f6f6;border:1px solid #d8d8d8}
.register h3{position:absolute;left:12px;top:12px;font-family:'Ubuntu',sans-serif;font-weight:500;font-size:16px;color:var(--orange)}
.register p{position:absolute;left:12px;top:38px;width:108px;font-size:7.6px;line-height:11px;color:#444}
.register .cta{position:absolute;left:12px;top:77px;width:61px;height:15px;background:#222;color:#fff;font-size:7.5px;display:flex;align-items:center;justify-content:center}
.register .badge{position:absolute;left:117px;top:27px;width:45px;height:45px;border-radius:5px;background:linear-gradient(#3ea2e6,#1669b5);color:#fff;font-size:7px;display:flex;align-items:flex-end;justify-content:center;padding-bottom:5px}

.cta-band{left:0;top:869px;width:985px;height:64px;background:linear-gradient(180deg,#f9862a,#ec5f0b)}
.cta-band .line{position:absolute;left:595px;top:0;width:1px;height:64px;background:rgba(0,0,0,.2)}
.cta-text{left:197px;top:887px;font-family:'Ubuntu',sans-serif;font-weight:500;font-size:19px;color:#fff;text-shadow:0 1px 1px rgba(0,0,0,.25)}
.order-btn{left:631px;top:880px;width:157px;height:44px;background:linear-gradient(#fafafa,#cfcfcf);border-radius:2px;display:flex;align-items:center;justify-content:center;font-style:italic;font-weight:700;font-size:18px;color:#444}

.disclaimer{left:197px;top:942px;width:592px;height:205px;background:#f0f0f0;border:1px solid #dcdcdc;border-radius:3px;padding:8px 9px;font-size:7.6px;line-height:11.1px;color:#a3a3a3}
.disclaimer strong{color:#444;font-weight:400;font-size:8.5px}
.disclaimer p{margin-bottom:11px}

.footer{left:0;top:1157px;width:985px;height:43px;background:var(--footer);color:#fff;font-size:8px;text-align:center}
.footer nav{margin-top:11px;display:flex;justify-content:center;gap:9px}
.footer small{display:block;margin-top:4px;font-size:8px}
</style>
</head>
<body>
<div class="abs topline"></div>
<header class="abs header"></header>
<div class="abs brand"><span class="brand-mark"></span><span class="brand-name">Veldora FX Ltd.</span></div>
<div class="abs brand-tag">From Traders to Traders, THE REAL DEAL</div>
<div class="abs btn-sm btn-login">Login</div>
<div class="abs btn-sm btn-register">Register</div>
<div class="abs btn-sm btn-lang">English<svg width="6" height="4"><path d="M0 0h6L3 4z" fill="#fff"/></svg></div>
<nav class="abs nav">
  <span class="active">Home</span><span>About Us</span><span>Order</span><span>Performance »</span><span>Arlo Brandt Special</span><span>Why Us?</span><span>Contact Us</span>
</nav>

<section class="abs hero">
  <div class="abs hero-photo" role="img" aria-label="Advisor in a grey suit sitting at a laptop in an office"></div>
</section>
<div class="abs hero-copy">
  <div class="hero-l1">BECAUSE IT IS ALL ABOUT</div>
  <div class="hero-l2">WHO IS TRADING</div>
  <div class="hero-l3">on YOUR Account</div>
</div>
<svg class="abs arrow arrow-left" width="34" height="34"><circle cx="17" cy="17" r="17" fill="#f39a28"/><path d="M20 10l-7 7 7 7" stroke="#fff" stroke-width="1.5" fill="none"/></svg>
<svg class="abs arrow arrow-right" width="34" height="34"><circle cx="17" cy="17" r="17" fill="#f39a28"/><path d="M14 10l7 7-7 7" stroke="#fff" stroke-width="1.5" fill="none"/></svg>

<div class="abs page-pattern" role="img" aria-label="Faint pattern of finance symbols and charts"></div>
<svg class="abs hero-curve" width="985" height="40"><path d="M0 12 L190 12 Q492 40 795 12 L985 12 L985 40 L0 40Z" fill="#f2f2f2"/><path d="M190 12 Q492 40 795 12 L795 40 L190 40Z" fill="#fff"/><path d="M0 11 L190 11 Q492 40 795 11 L985 11" stroke="#f7931e" stroke-width="2" fill="none"/></svg>
<main class="abs panel"></main>

<p class="abs intro">Veldora FX LTD is the ONLY forex signal service on this planet that provides full info about the traders involved including REAL personal photos, REAL personal details and portfolios, as well as YEARS of verified and consistent live trading performance.</p>

<section class="abs signals">
  <h2>How Signals Work</h2>
  <div class="signals-body">
    <div class="signals-img" role="img" aria-label="Hand holding a tablet with a world map and connected traders"></div>
    Once you subscribe, you will be re-directed to a secure page to download and set-up the EA copier on your VPS with all the instructions you need(We provide full support, and we can set it up for you for no additional charge. Once set-up, the software is of superior quality and copies flawlessly, and you have direct and total control over your account.
    Whereas your subscription will be renewed automatically by the end of the cycle you choose (Monthly/OR/4 months). Furthermore, you can adjust the risk set-up according to your own risk tolerance (We provide excellent and fast customer support to answer any question you may have). Nevertheless, you can unsubscribe anytime you want. And you keep 100% of the profits on your account regardless. And with no obligation.
  </div>
</section>
<aside class="abs brokers">
  <h3>Brokers option:</h3>
  <p>You can choose any broker you like, the copying software will work on your existing broker and existing accounts. The copier can support nearly every broker out there.</p>
</aside>

<div class="abs divider"></div>
<div class="abs feature f1"><div class="icon"><svg width="24" height="22"><rect x="2" y="14" width="3" height="7" fill="#d9261c"/><rect x="7" y="11" width="3" height="10" fill="#d9261c"/><rect x="12" y="8" width="3" height="13" fill="#d9261c"/><rect x="17" y="4" width="3" height="17" fill="#d9261c"/><path d="M2 12L20 1" stroke="#d9261c" stroke-width="1.5"/></svg></div><h4>Forex Inside</h4><p>Lorem Ipsum is simply dummy text of the printing and typesetting industry.</p></div>
<div class="abs feature f2"><div class="icon"><svg width="26" height="26"><circle cx="12" cy="12" r="10" fill="#fff" stroke="#333" stroke-width="2"/><path d="M19 19l6 6" stroke="#333" stroke-width="3"/></svg></div><h4>Live Analytics</h4><p>Lorem Ipsum has been the industry's standard dummy text ever since the 1500s, when an unknown printer.....</p></div>
<div class="abs feature f3"><div class="icon"><svg width="26" height="26"><rect x="1" y="1" width="24" height="24" rx="5" fill="#2a8fd8"/><rect x="7" y="5" width="12" height="10" fill="#cfe8fb"/></svg></div><h4>Useful Links</h4><p>Lorem Ipsum is simply dummy text of the printing and typesetting industry.</p></div>
<div class="abs feature f4"><div class="icon"><svg width="22" height="26"><rect x="2" y="1" width="18" height="24" rx="2" fill="#fff" stroke="#333"/><path d="M5 6h12M5 10h12M5 14h12M5 18h8" stroke="#999"/></svg></div><h4>News and Updates</h4><p>Lorem Ipsum has been the industry's standard dummy text ever since the 1500s, when an unknown printer.....</p></div>

<aside class="abs register">
  <h3>Register Free</h3>
  <p>Registration is quick and easy. Access live customer rates, free tools.</p>
  <div class="cta">Register Now</div>
  <div class="badge">Newsletter</div>
</aside>

<section class="abs cta-band"><div class="line"></div></section>
<div class="abs cta-text">Let us do the&nbsp; picks, while you enjoy the ride!</div>
<div class="abs order-btn">Order Now</div>

<section class="abs disclaimer">
  <p><strong>Risk Disclaimer :</strong> All results on this web site must be regarded as hypothetical. hypothetical performance results have many inherent limitations, some of which are described below.</p>
  <p>no representation is being made that any account will or is likely to achieve profits or losses similar to those shown. in fact, there are frequently sharp differences between hypothetical performance results and the actual results subsequently achieved by any particular trading program. one of the limitations of hypothetical performance results is that they are generally prepared with the benefit of hindsight. in addition, hypothetical trading does not involve financial risk, and no hypothetical trading record can completely account for the impact of financial risk in actual trading. for example, the ability to withstand losses or to adhere to a particular trading program in spite of trading losses are material points which can also adversely affect actual trading results. there are numerous other factors related to the markets in general or to the implementation of any specific trading program which cannot be fully accounted for in the preparation of hypothetical performance results and all of which can adversely affect actual trading results. past results are not necessarily indicative of future results.</p>
  <p>Trading foreign exchange on margin carries a high level of risk, and may not be suitable for all investors. the high degree of leverage can either work against you or on your behalf. before deciding to invest in foreign exchange you should carefully consider your investment objectives, level of experience, and risk appetite. the possibility exists that you could sustain a loss of some or all of your initial investment and therefore you should not invest money that you cannot afford to lose. you should be aware of all the risks associated with foreign exchange trading, and seek advice from an independent financial advisor if you have any doubts.</p>
</section>

<footer class="abs footer">
  <nav><span>Home</span><span>About Us</span><span>Order</span><span>Performance</span><span>Arlo Brandt Special</span><span>Terms &amp; Conditions</span><span>Why Us?</span><span>Contact Us</span></nav>
  <small>Copyright 2013, VeldoraFx LTD</small>
</footer>
</body>
</html>
```